Homepage for the brisk-find Web Application

At the end of this text, you will find a link to a website that is under construction for a webApp that I intend to launch soon. The contest goal is for you to make redesign the homepage in a nice, fresh, modern Style. Only design, no coding necessary. It needs to have a responsive version for small screens like smart phones. Attached is the text for it, and some images that you may use. You are welcome to find or create additional supporting images. You can use PixTrove.example or similar service to find new images as long as I can purchase the non-exclusive use rights for the images at similar prices. The contest is just for the home page. However, the winner, if I like the work and we can agree on a fair price, could be contracted on a one-on-one basis to do the rest of the site. You are welcome to suggest minor changes like font sizes and minor variations on the Header banner, but that banner is consistent with the user interface of the application therefore should not change too much. The information should flow somewhat continually without much use of side bars or things like that.
https://www.brisk-find.example
Sincerely,
Marco D. Ferral

```html
<!DOCTYPE html>
<html lang="en">
<head>
<meta charset="utf-8">
<title>Brisk-Find — Find any document or item instantly</title>
<link href="https://fonts.googleapis.com/css2?family=Poppins:wght@400;500;600&display=swap" rel="stylesheet">
<style>
:root{
  --brand-blue:#2f7cc6;
  --nav-blue:#0c6db5;
  --accent:#fb7d5b;
  --ink:#111111;
  --body:#222222;
  --mist:#dcfafc;
  --mist-deep:#bff1f6;
  --white:#ffffff;
  --footer:#000000;
}
*{box-sizing:border-box;margin:0;padding:0}
html,body{width:1200px;height:3571px;overflow:hidden;background:var(--white)}
body{position:relative;font-family:"Poppins",sans-serif;color:var(--body)}
.abs{position:absolute}
.accent{color:var(--accent)}

/* header */
.topbar{left:0;top:0;width:1200px;height:69px;background:var(--brand-blue)}
.brand{left:97px;top:16px;display:flex;align-items:center;gap:6px;color:var(--white);font-size:24px;font-weight:400}
.brand-dot{width:30px;height:30px;border-radius:50%;background:var(--white)}
.field{top:21px;width:303px;height:29px;border-radius:15px;background:var(--white);border:none;font-family:inherit;font-size:12px;color:#333;padding-left:17px;display:flex;align-items:center}
.login{left:1005px;top:21px;width:98px;height:29px;border:2px solid var(--accent);border-radius:15px;color:var(--accent);font-size:13px;display:flex;align-items:center;justify-content:center}
.navbar{left:0;top:69px;width:1200px;height:25px;background:var(--nav-blue)}
.nav-link{top:73px;color:var(--white);font-size:12px}

/* hero */
.hero-title{left:97px;top:190px;font-size:50px;font-weight:600;line-height:70px;color:var(--ink)}
.hero-text{left:97px;top:345px;width:470px;font-size:16px;line-height:26px}
.btn{display:flex;align-items:center;justify-content:center;border-radius:18px;font-size:12.5px}
.btn-solid{background:var(--accent);color:var(--white)}
.btn-outline{border:2px solid var(--accent);color:var(--accent);background:var(--white)}

.illus{border-radius:50%;background:radial-gradient(circle at 50% 50%,var(--mist) 0 68%,var(--mist-deep) 69% 70%,var(--mist) 71%);box-shadow:0 0 0 2px #eafcfd}

/* section headings */
.section-title{left:0;width:1200px;text-align:center;font-size:36px;font-weight:600;line-height:52px;color:var(--ink)}
.block-title{font-size:27px;font-weight:500;color:var(--ink)}
.block-text{font-size:14.5px;line-height:24.1px}

/* accordion */
.acc-item{left:137px;width:458px;height:43px;border-radius:22px;background:var(--white);box-shadow:0 2px 8px rgba(0,0,0,.14);display:flex;align-items:center;justify-content:space-between;padding:0 20px 0 26px;font-size:13.5px;color:var(--ink)}
.acc-plus{color:var(--accent);font-size:20px;line-height:1}

/* benefits */
.benefit{display:flex;gap:14px;font-size:17.5px;line-height:24px;color:var(--ink)}
.benefit svg{flex:0 0 26px;margin-top:2px}

.footer{left:0;top:2816px;width:1200px;height:47px;background:var(--footer);color:var(--white);font-size:14px;display:flex;align-items:center;justify-content:center}
</style>
</head>
<body>

<header>
  <div class="abs topbar"></div>
  <div class="abs brand"><span class="brand-dot"></span><span>Brisk Find</span></div>
  <div class="abs field" style="left:298px">Username</div>
  <div class="abs field" style="left:636px">Password</div>
  <div class="abs login">login</div>
  <nav>
    <div class="abs navbar"></div>
    <span class="abs nav-link" style="left:325px">About</span>
    <span class="abs nav-link" style="left:386px">Pricing</span>
    <span class="abs nav-link" style="left:454px">Blog</span>
    <span class="abs nav-link" style="left:509px">FAQs</span>
    <span class="abs nav-link" style="left:567px">Support</span>
    <span class="abs nav-link" style="left:643px">Reviews</span>
    <span class="abs nav-link" style="left:718px">Contact Us</span>
    <span class="abs nav-link" style="left:816px">Free-Trial</span>
  </nav>
</header>

<section class="hero">
  <h1 class="abs hero-title">Find any document or<br>item <span class="accent">instantly!</span></h1>
  <p class="abs hero-text">Brisk-Find is a system that allows you to quickly search for the location of every item that you store or file. It is an essential tool for keeping track of paper documents or any other kind of physical item.</p>
  <div class="abs btn btn-solid" style="left:97px;top:475px;width:115px;height:34px">Get Pricing</div>
  <div class="abs btn btn-outline" style="left:238px;top:475px;width:114px;height:34px">Free Trial</div>
  <div class="abs illus" style="left:676px;top:137px;width:438px;height:438px" role="img" aria-label="Illustration of a businessman pulling a folder from a laptop filing cabinet"></div>
</section>

<section>
  <h2 class="abs section-title" style="top:618px">Why use a storage management system<br>like <span class="accent">Brisk-Find?</span></h2>
  <div class="abs illus" style="left:64px;top:757px;width:438px;height:438px" role="img" aria-label="Illustration of a businessman holding a binder beside a phone with file drawers"></div>
  <h3 class="abs block-title" style="left:577px;top:790px">Managing paper documents</h3>
  <p class="abs block-text" style="left:577px;top:839px;width:524px">It is quite common for most people and businesses to receive a variety of such documents that need to be filed. The problem is how to efficiently do it in a way that any of it can easily be found, even in a distant future. We normally put them in folders on file drawers sorted by some criteria. But which criterion is the right standard for all kinds of documents? There is no right criterion for every kind of document. It is necessary to use a combination of them. If after some time you do not remember which criterion you used to file a document, you may have a hard time finding it, or not find it at all. This problem is greatly intensified when the person looking for the document is not the same person that filed it. It is estimated that workers spend over 20% of their time managing documents. A storage management system like Brisk-Find would allow any authorized user to instantly find any document regardless of who filed it or which criterion was used, as long as it was properly filed using the system.</p>
</section>

<section>
  <h3 class="abs block-title" style="left:137px;top:1269px">Managing any non-document objects</h3>
  <p class="abs block-text" style="left:137px;top:1323px;width:440px">The same is true of storing any other kind of objects. Common examples include</p>
  <div class="abs acc-item" style="top:1397px"><span>Storage boxes, closets, warehouses, and shelves</span><span class="acc-plus">+</span></div>
  <div class="abs acc-item" style="top:1453px"><span>Books</span><span class="acc-plus">+</span></div>
  <div class="abs acc-item" style="top:1510px"><span>Wines</span><span class="acc-plus">+</span></div>
  <div class="abs acc-item" style="top:1567px"><span>Safety boxes</span><span class="acc-plus">+</span></div>
  <div class="abs acc-item" style="top:1623px"><span>Moving boxes</span><span class="acc-plus">+</span></div>
  <div class="abs acc-item" style="top:1680px"><span>Test samples</span><span class="acc-plus">+</span></div>
  <div class="abs acc-item" style="top:1737px"><span>Audio, video, data, and removable media</span><span class="acc-plus">+</span></div>
  <div class="abs acc-item" style="top:1793px"><span>Keys</span><span class="acc-plus">+</span></div>
  <div class="abs illus" style="left:734px;top:1336px;width:436px;height:436px" role="img" aria-label="Illustration of a businessman carrying a test tube beside a phone with file drawers"></div>
</section>

<section>
  <div class="abs illus" style="left:62px;top:1925px;width:438px;height:438px" role="img" aria-label="Illustration of a businessman holding a wine bottle beside a phone with file drawers"></div>
  <h2 class="abs" style="left:607px;top:1992px;font-size:36px;font-weight:600;line-height:49px;color:var(--ink)">Alternative uses for<br><span class="accent">Brisk-Find</span></h2>
  <p class="abs block-text" style="left:607px;top:2124px;width:436px">How many times have you gone to a restaurant and couldn't recall how good (or bad) each of the dishes were that you previously ordered? You can use Brisk-Find to record each one to improve your experience for every visit. Our app can also help you decide where you want to go or which dish to recommend when you have a special occasion.</p>
  <div class="abs btn btn-solid" style="left:607px;top:2293px;width:123px;height:31px;font-size:13.5px">Get Started</div>
</section>

<section>
  <h2 class="abs section-title" style="top:2412px">Why <span class="accent">Brisk-Find?</span></h2>
  <svg width="0" height="0" style="position:absolute"><defs><symbol id="tick" viewBox="0 0 26 20"><path d="M2 10 L10 17 L24 3" fill="none" stroke="#fb7d5b" stroke-width="4" stroke-linecap="round" stroke-linejoin="round"/></symbol></defs></svg>
  <div class="abs" style="left:96px;top:2523px;width:460px;display:flex;flex-direction:column;gap:12px">
    <div class="benefit"><svg width="26" height="20"><use href="#tick"/></svg><span>It is extremely easy to use.</span></div>
    <div class="benefit"><svg width="26" height="20"><use href="#tick"/></svg><span>It's very affordable. Checkout our pricing plans!</span></div>
    <div class="benefit"><svg width="26" height="20"><use href="#tick"/></svg><span>Since it is online, your data is available almost anywhere in the world.</span></div>
  </div>
  <div class="abs" style="left:640px;top:2523px;width:470px;display:flex;flex-direction:column;gap:12px">
    <div class="benefit"><svg width="26" height="20"><use href="#tick"/></svg><span>It Adapts to your stile. Since each catalog can have 1 or more levels of depth (folders and sub-folders), Brisk-Find does not force you to use a specific filing or storage methodology.</span></div>
    <div class="benefit"><svg width="26" height="20"><use href="#tick"/></svg><span>Data encryption ensures that your information is always private, safe, and secure.</span></div>
  </div>
  <div class="abs btn btn-solid" style="left:503px;top:2735px;width:193px;height:39px;border-radius:20px;font-size:17px;box-shadow:0 3px 8px rgba(251,125,91,.45)">30 Days Free Trial</div>
</section>

<footer class="abs footer">© Copyright 2021 Brisk-find .All Rights Reserved.</footer>

</body>
</html>
```